Contemporary Business card for Event Manager

Needed for my startup events company in Melbourne. Events I manage will be based within the fashion industry, sporting events, product launches etc. Not weddings or small dinner parties. Therfore I am after something professional and aimed at high end corporate market; but with the added emphasis on not being too conservative or boring. I am happy with a pop of colour e.g. yellow or copper foil.

Target Market(s)

fashion industry, design industry, high end sporting events e.g. Polo, Grand Prix, corporate clients,

Industry/Entity Type

Fashion

Contact Information for Business Card

side 1
Lucy Brandt (can be upper or lower case, have a feature full stop between first and surname, or at the end of the nameetc) I am open to ideas. I would also be fine with my initials or name as a logo on the front (if this is the case my full name would need to go on the second side of the card.
2nd side:
Mobile: +61 400 817 263
email: lucy.brandt@mailnest.com.au

on one side of the card:
event management | brand activation | Advisory Services

Font styles to use
Serif
Sans Serif

Requirements
Must have
• side 2 must have
• mobile number
• email address
• event management | brand activation | Advisory Services
• ** my full name (Lucy Brandt) must be on the card somewhere)
Nice to have
• 1st side
• I see the card stock being either a dark grey, light grey, natural white or black (all matt colours on unprocessed card). I see the writing being copper foil, or foil white or foil black.
• To give you a feel for me, think: contemporary, minimalist, I love line drawings, concrete, white with grey vein marble, copper, white, grey, black...yes I do like colour....yellow (but pops of colour) ;) I would like the card to look designer but 'on trend' as I deal with a lot of design and fashion clients....styles - think the sophistication and simplicity of Vireaux or urban contemporary.
• some examples of what I like. Although please don't leet this limit you...I really am happy to have something a little more urban or design focused like a line drawing of an object, person too or a photo image too.
• https://www.moodtackle.com/pin/830165427719302846/
• https://www.moodtackle.com/pin/607281935540173268/
• https://www.moodtackle.com/pin/318746205913457092/
• https://www.moodtackle.com/pin/41983627530918476/
• https://www.moodtackle.com/pin/53128940672419087/
• https://www.moodtackle.com/pin/90316284750638152/
• https://www.moodtackle.com/pin/734092618450362918/
• https://www.moodtackle.com/pin/926354081736215407/
• https://www.moodtackle.com/pin/481627093518704356/
Should not have
• should not look commercial or have cartoonish looking logos. However happy with a simple line drawing or logo with initials etc.

```html
<!DOCTYPE html>
<html lang="en">
<head>
<meta charset="utf-8">
<title>Lucy Brandt — Business Card</title>
<link rel="stylesheet" href="https://fonts.googleapis.com/css2?family=Jost:wght@300;400;500&display=swap">
<style>
  :root {
    --backdrop: #d6d6d6;
    --card-stock: #050505;
    --foil-white: #f4f4f4;
    --foil-soft: #e2e2e2;
  }
  * { margin: 0; padding: 0; box-sizing: border-box; }
  html, body {
    width: 1200px;
    height: 862px;
    overflow: hidden;
    background: var(--backdrop);
  }
  .card-spread {
    position: relative;
    width: 1200px;
    height: 862px;
    display: flex;
    justify-content: center;
    align-items: center;
    gap: 110px;
  }
  .card {
    position: relative;
    width: 330px;
    height: 540px;
    background: var(--card-stock);
    color: var(--foil-white);
    font-family: "Jost", "Futura", sans-serif;
    text-transform: uppercase;
  }
  .card-front .holder-name {
    position: absolute;
    left: 60px;
    top: 258px;
    font-weight: 500;
    font-size: 31px;
    line-height: 1.45;
    letter-spacing: 0.02em;
  }
  .card-front .holder-name span { display: block; }
  .card-front .holder-name .given { padding-left: 10px; }
  .card-back .contact {
    position: absolute;
    left: 44px;
    top: 118px;
    font-weight: 300;
    font-size: 16px;
    line-height: 1.55;
    color: var(--foil-soft);
    list-style: none;
  }
  .card-back .contact .phone { padding-left: 6px; letter-spacing: 0.04em; }
  .card-back .contact .email { font-size: 15px; letter-spacing: 0.01em; }
  .card-back .services {
    position: absolute;
    left: 40px;
    top: 418px;
    list-style: none;
    font-weight: 300;
    font-size: 15px;
    line-height: 1;
    color: var(--foil-soft);
  }
  .card-back .services li {
    display: flex;
    align-items: center;
    gap: 10px;
    margin-bottom: 12px;
  }
  .card-back .services li:nth-child(2) { padding-left: 0; }
  .card-back .services svg { width: 16px; height: 16px; flex: none; }
</style>
</head>
<body>
  <main class="card-spread">
    <section class="card card-front" aria-label="Card front">
      <h1 class="holder-name">
        <span class="given">Lucy</span>
        <span class="family">Brandt.</span>
      </h1>
    </section>

    <section class="card card-back" aria-label="Card back">
      <ul class="contact">
        <li class="phone">+61 400 817 263</li>
        <li class="email">lucy.brandt@mailnest.com.au</li>
      </ul>
      <ul class="services">
        <li>
          <svg viewBox="0 0 20 20" aria-hidden="true"><polygon points="10,1 12.4,7.3 19,7.6 13.8,11.7 15.6,18.2 10,14.4 4.4,18.2 6.2,11.7 1,7.6 7.6,7.3" fill="none" stroke="#e2e2e2" stroke-width="1.4"/></svg>
          Event Management
        </li>
        <li>
          <svg viewBox="0 0 20 20" aria-hidden="true"><polygon points="10,1 12.4,7.3 19,7.6 13.8,11.7 15.6,18.2 10,14.4 4.4,18.2 6.2,11.7 1,7.6 7.6,7.3" fill="none" stroke="#e2e2e2" stroke-width="1.4"/></svg>
          Brand Activation
        </li>
        <li>
          <svg viewBox="0 0 20 20" aria-hidden="true"><polygon points="10,1 12.4,7.3 19,7.6 13.8,11.7 15.6,18.2 10,14.4 4.4,18.2 6.2,11.7 1,7.6 7.6,7.3" fill="none" stroke="#e2e2e2" stroke-width="1.4"/></svg>
          Advisory Services
        </li>
      </ul>
    </section>
  </main>
</body>
</html>
```